Diabetes control iOS/Android app design

I need a modern app design with light colors that are easy on the eyes, This app is for diabetes control. Focusing on Sweet/carb control and its daily intake .. I have uploaded some wireframe pages to design . Light colors are preferred for design. I donot need too much Hussle and data on main page.
Name/title: Glimwell- Diabetes reversal

Target Market(s)

Diabetes patients

Industry/Entity Type

health

Colors
0094D4
00A9DD
6FCCEA
C7EBF8
E9F6FB
00AB8E
00BBA5
67D7C9
C6EFE9
E9F9F6
59FF00
82FF00
B8FF75
E3FFCB
F4FFEA
FFC000
F8CF3A
FAE287
FDF2CF
FEFAEE

Requirements
Should not have
• complicated design. It should be simple , modern and easy o eye.

```html
<!DOCTYPE html>
<html lang="en">
<head>
<meta charset="utf-8">
<title>Glimwell - Diabetes reversal</title>
<link href="https://fonts.googleapis.com/css2?family=Inter:wght@400;500;600;700&display=swap" rel="stylesheet">
<style>
  :root{
    --backdrop:#353535;
    --white:#ffffff;
    --ink:#1b1b1f;
    --muted:#6b6f76;
    --line:#e6eaee;
    --blue:#2290cf;
    --blue-deep:#1f7fc4;
    --teal:#1ba48e;
    --teal-mid:#20a3a0;
    --sky-soft:#e4f4fb;
    --bar-idle:#e9ecf0;
    --amber:#f5b52a;
    --danger:#e53935;
    --warn:#f2c12e;
    --ok:#5cbf2f;
  }
  *{box-sizing:border-box;margin:0;padding:0}
  html,body{width:1200px;height:886px;overflow:hidden;background:var(--backdrop);font-family:"Inter",sans-serif;color:var(--ink)}
  .stage{position:absolute;left:0;top:0;width:1376px;height:1016px;transform:scale(0.872);transform-origin:0 0}
  .screen{position:absolute;width:375px;background:var(--white);overflow:hidden}
  .screen--home{left:85px;top:79px;height:812px}
  .screen--monitor{left:500px;top:79px;height:857px}
  .screen--plan{left:915px;top:79px;height:812px}
  .abs{position:absolute}
  .status-time{position:absolute;left:30px;top:14px;font-size:15px;font-weight:600}
  .status-icons{position:absolute;right:16px;top:16px}
  .nav-back{position:absolute;left:22px;top:63px}
  .nav-title{position:absolute;left:0;right:0;top:62px;text-align:center;font-size:17px;font-weight:600}

  /* home */
  .hero{position:absolute;left:0;top:0;width:375px;height:296px;background:linear-gradient(160deg,#1f8fd0 0%,#1d9db6 55%,#1aa48f 100%)}
  .hero .status-time,.hero .status-icons{color:var(--white)}
  .avatar{position:absolute;left:24px;top:52px;width:40px;height:40px;border-radius:8px;background:linear-gradient(135deg,#c9d2da,#7d6a5d)}
  .greet{position:absolute;left:72px;top:56px;color:var(--white)}
  .greet small{display:block;font-size:11px;font-weight:400}
  .greet strong{display:block;font-size:13px;font-weight:600;margin-top:2px}
  .bell{position:absolute;left:311px;top:52px;width:40px;height:40px;border-radius:8px;background:rgba(255,255,255,.22);display:flex;align-items:center;justify-content:center}
  .hero-title{position:absolute;left:0;right:0;top:140px;text-align:center;color:var(--white);font-size:26px;font-weight:700}
  .ring{position:absolute;left:80px;top:188px;width:216px;height:216px;border-radius:50%;background:linear-gradient(180deg,#1fa2a4,#1a9a8c)}
  .dial{position:absolute;left:102px;top:210px;width:172px;height:172px;border-radius:50%;background:var(--white);box-shadow:0 6px 18px rgba(0,0,0,.12);text-align:center}
  .dial-count{font-size:32px;font-weight:600;color:var(--blue);margin-top:34px}
  .dial-label{font-size:17px;line-height:25px;margin-top:4px}
  .section-title{position:absolute;left:0;right:0;top:438px;text-align:center;font-size:20px;font-weight:600}
  .gauge-label{position:absolute;font-size:13px;font-weight:600;line-height:16px}

  /* tab bar */
  .tabbar{position:absolute;left:0;width:375px;height:90px;background:var(--white);border-radius:22px 22px 0 0;box-shadow:0 -6px 18px rgba(0,0,0,.06)}
  .tab{position:absolute;width:70px;text-align:center;font-size:11px;font-weight:500;color:#333}
  .tab svg{display:block;margin:0 auto 4px}
  .tab--active{color:var(--amber)}
  .tab--current{font-weight:700}
  .fab{position:absolute;width:44px;height:44px;background:var(--blue);border-radius:9px;transform:rotate(45deg);box-shadow:0 6px 14px rgba(34,144,207,.35);display:flex;align-items:center;justify-content:center}
  .fab svg{transform:rotate(-45deg)}
  .home-indicator{position:absolute;width:128px;height:4px;border-radius:2px;background:#c8c8c8}

  /* monitor */
  .card{position:absolute;left:23px;width:329px;border:1px solid var(--line);border-radius:10px;background:var(--white);box-shadow:0 2px 8px rgba(0,0,0,.04);overflow:hidden}
  .card-title{position:absolute;left:0;right:0;top:18px;text-align:center;font-size:14px;font-weight:600}
  .axis{position:absolute;font-size:10px;color:#555;text-align:center;width:30px}
  .tip{position:absolute;background:var(--white);border:1px solid var(--line);border-radius:4px;font-size:10px;color:#444}
  .stat{position:absolute;top:668px;width:155px;height:66px;border:1px solid var(--line);border-radius:10px;background:var(--white)}
  .stat-head{position:absolute;left:14px;top:10px;display:flex;align-items:center;gap:8px}
  .stat-badge{width:22px;height:22px;border-radius:5px;display:flex;align-items:center;justify-content:center}
  .stat-value{font-size:24px;font-weight:700}
  .stat-unit{font-size:12px;color:var(--muted)}
  .stat-note{position:absolute;left:14px;top:44px;font-size:11px;color:var(--muted)}

  /* plan */
  .portrait{position:absolute;left:141px;top:134px;width:94px;height:94px;border-radius:50%;background:linear-gradient(160deg,#a9b6c0,#3c4a57)}
  .plan-title{position:absolute;left:0;right:0;top:254px;text-align:center;font-size:20px;font-weight:700}
  .plan-sub{position:absolute;left:50px;right:50px;top:292px;text-align:center;font-size:13px;line-height:17px;color:#555}
  .steps-title{position:absolute;left:23px;top:367px;font-size:16px;font-weight:600}
  .step{position:absolute;left:23px;width:329px;height:51px;background:var(--sky-soft);border-radius:3px;display:flex;align-items:center;gap:10px;padding-left:20px;color:var(--blue);font-size:14px;font-weight:500}
  .step small{font-size:10px}
</style>
</head>
<body>
<div class="stage">

  <!-- Home: Sugar Count -->
  <section class="screen screen--home">
    <div class="hero">
      <span class="status-time">9:41</span>
      <svg class="status-icons" width="66" height="12" viewBox="0 0 66 12" fill="#fff"><rect x="0" y="8" width="3" height="4" rx="1"/><rect x="5" y="6" width="3" height="6" rx="1"/><rect x="10" y="3" width="3" height="9" rx="1"/><rect x="15" y="0" width="3" height="12" rx="1"/><path d="M30 11l-2-2a3 3 0 0 1 4 0z M25 6a7.5 7.5 0 0 1 10 0l-1.5 1.5a5.5 5.5 0 0 0-7 0z M22 3a12 12 0 0 1 16 0l-1.5 1.5a10 10 0 0 0-13 0z"/><rect x="44" y="1" width="20" height="10" rx="3" fill="none" stroke="#fff"/><rect x="46" y="3" width="16" height="6" rx="1.5"/></svg>
      <div class="avatar" role="img" aria-label="User profile photo"></div>
      <div class="greet"><small>Hello Sam Rivera</small><strong>Wednesday, 08 Jan</strong></div>
      <div class="bell"><svg width="20" height="20" viewBox="0 0 24 24" fill="none" stroke="#fff" stroke-width="1.6"><path d="M6 16V11a6 6 0 0 1 12 0v5l1.5 2h-15z"/><path d="M10 20a2 2 0 0 0 4 0"/></svg></div>
      <div class="hero-title">Sugar Count</div>
    </div>
    <div class="ring"></div>
    <div class="dial">
      <div class="dial-count">01</div>
      <div class="dial-label">Sugar Today<br>Bite</div>
    </div>
    <div class="section-title">Consumption Today</div>
    <div class="gauge-label" style="left:0;right:0;top:485px;text-align:center">Fatal</div>
    <div class="gauge-label" style="left:27px;top:648px">Danger</div>
    <div class="gauge-label" style="left:284px;top:648px">Catastrophe</div>
    <svg class="abs" style="left:0;top:0" width="375" height="812" viewBox="0 0 375 812">
      <path d="M48 631 A141 141 0 0 1 327 631" fill="none" stroke="var(--blue)" stroke-width="5" stroke-linecap="round"/>
      <g stroke-width="2" stroke-linecap="round">
        <line x1="187.5" y1="525" x2="187.5" y2="534" stroke="var(--danger)" transform="rotate(-80 187.5 649)"/>
        <line x1="187.5" y1="525" x2="187.5" y2="534" stroke="var(--danger)" transform="rotate(-72 187.5 649)"/>
        <line x1="187.5" y1="525" x2="187.5" y2="534" stroke="var(--danger)" transform="rotate(-64 187.5 649)"/>
        <line x1="187.5" y1="525" x2="187.5" y2="542" stroke="var(--danger)" transform="rotate(-56 187.5 649)"/>
        <line x1="187.5" y1="525" x2="187.5" y2="534" stroke="var(--danger)" transform="rotate(-48 187.5 649)"/>
        <line x1="187.5" y1="525" x2="187.5" y2="534" stroke="var(--danger)" transform="rotate(-40 187.5 649)"/>
        <line x1="187.5" y1="525" x2="187.5" y2="534" stroke="var(--warn)" transform="rotate(-32 187.5 649)"/>
        <line x1="187.5" y1="525" x2="187.5" y2="542" stroke="var(--warn)" transform="rotate(-24 187.5 649)"/>
        <line x1="187.5" y1="525" x2="187.5" y2="534" stroke="var(--warn)" transform="rotate(-16 187.5 649)"/>
        <line x1="187.5" y1="525" x2="187.5" y2="534" stroke="var(--warn)" transform="rotate(-8 187.5 649)"/>
        <line x1="187.5" y1="525" x2="187.5" y2="545" stroke="var(--warn)"/>
        <line x1="187.5" y1="525" x2="187.5" y2="534" stroke="var(--warn)" transform="rotate(8 187.5 649)"/>
        <line x1="187.5" y1="525" x2="187.5" y2="534" stroke="var(--warn)" transform="rotate(16 187.5 649)"/>
        <line x1="187.5" y1="525" x2="187.5" y2="542" stroke="var(--warn)" transform="rotate(24 187.5 649)"/>
        <line x1="187.5" y1="525" x2="187.5" y2="534" stroke="var(--warn)" transform="rotate(32 187.5 649)"/>
        <line x1="187.5" y1="525" x2="187.5" y2="534" stroke="var(--ok)" transform="rotate(40 187.5 649)"/>
        <line x1="187.5" y1="525" x2="187.5" y2="534" stroke="var(--ok)" transform="rotate(48 187.5 649)"/>
        <line x1="187.5" y1="525" x2="187.5" y2="542" stroke="var(--ok)" transform="rotate(56 187.5 649)"/>
        <line x1="187.5" y1="525" x2="187.5" y2="534" stroke="var(--ok)" transform="rotate(64 187.5 649)"/>
        <line x1="187.5" y1="525" x2="187.5" y2="534" stroke="var(--ok)" transform="rotate(72 187.5 649)"/>
        <line x1="187.5" y1="525" x2="187.5" y2="534" stroke="var(--ok)" transform="rotate(80 187.5 649)"/>
      </g>
      <polygon points="230,553 190,643 184,639" fill="var(--teal)"/>
      <polygon points="184,643 190,643 173,667" fill="var(--teal)"/>
      <circle cx="187" cy="641" r="6" fill="#fff" stroke="#3a3f45" stroke-width="3"/>
    </svg>
    <nav class="tabbar" style="top:731px">
      <div class="tab tab--active tab--current" style="left:17px;top:17px"><svg width="18" height="18" viewBox="0 0 24 24" fill="var(--amber)"><path d="M12 3l9 7v11H3V10z"/><circle cx="12" cy="14" r="2" fill="#fff"/></svg>Home</div>
      <div class="tab" style="left:81px;top:17px"><svg width="18" height="18" viewBox="0 0 24 24" fill="none" stroke="#333" stroke-width="1.6"><path d="M3 3v18h18"/><path d="M6 16l4-5 4 3 6-7"/></svg>Monitors</div>
      <div class="tab" style="left:224px;top:17px"><svg width="18" height="18" viewBox="0 0 24 24" fill="none" stroke="#333" stroke-width="1.6"><rect x="4" y="3" width="16" height="18" rx="3"/><path d="M9 3v18M15 9l-2 3 2 3"/></svg>Goal</div>
      <div class="tab" style="left:288px;top:17px"><svg width="18" height="18" viewBox="0 0 24 24" fill="none" stroke="#333" stroke-width="1.6"><circle cx="12" cy="8" r="4"/><path d="M4 21a8 8 0 0 1 16 0"/></svg>Profile</div>
      <div class="home-indicator" style="left:124px;top:69px"></div>
    </nav>
    <div class="fab" style="left:166px;top:710px"><svg width="20" height="20" viewBox="0 0 20 20" stroke="#fff" stroke-width="2"><path d="M10 2v16M2 10h16"/></svg></div>
  </section>

  <!-- Rehab Monitor -->
  <section class="screen screen--monitor">
    <span class="status-time">9:41</span>
    <svg class="status-icons" width="66" height="12" viewBox="0 0 66 12" fill="#111"><rect x="0" y="8" width="3" height="4" rx="1"/><rect x="5" y="6" width="3" height="6" rx="1"/><rect x="10" y="3" width="3" height="9" rx="1"/><rect x="15" y="0" width="3" height="12" rx="1"/><path d="M30 11l-2-2a3 3 0 0 1 4 0z M25 6a7.5 7.5 0 0 1 10 0l-1.5 1.5a5.5 5.5 0 0 0-7 0z M22 3a12 12 0 0 1 16 0l-1.5 1.5a10 10 0 0 0-13 0z"/><rect x="44" y="1" width="20" height="10" rx="3" fill="none" stroke="#111"/><rect x="46" y="3" width="16" height="6" rx="1.5"/></svg>
    <svg class="nav-back" width="12" height="18" viewBox="0 0 12 18" fill="none" stroke="#333" stroke-width="1.6"><path d="M9 2L3 9l6 7"/></svg>
    <div class="nav-title">Rehab Monitor</div>

    <div class="card" style="top:116px;height:248px">
      <div class="card-title">Daily Sugar (Fasting + Random)</div>
      <div class="axis" style="left:17px;top:56px">Mon</div><div class="axis" style="left:17px;top:74px;font-weight:600;color:#222">10</div>
      <div class="axis" style="left:70px;top:56px">Tue</div><div class="axis" style="left:70px;top:74px;font-weight:600;color:#222">11</div>
      <div class="axis" style="left:123px;top:56px">Wed</div><div class="axis" style="left:123px;top:74px;font-weight:600;color:#222">12</div>
      <div class="axis" style="left:178px;top:56px">Thu</div><div class="axis" style="left:178px;top:74px;font-weight:600;color:#222">13</div>
      <div class="axis" style="left:226px;top:56px">Fri</div><div class="axis" style="left:226px;top:74px;font-weight:600;color:#222">14</div>
      <div class="axis" style="left:273px;top:56px">Sat</div><div class="axis" style="left:273px;top:74px;font-weight:600;color:#222">15</div>
      <svg class="abs" style="left:0;top:0" width="329" height="248" viewBox="0 0 329 248">
        <defs><linearGradient id="sugarFill" x1="0" y1="0" x2="0" y2="1"><stop offset="0" stop-color="#9fd8f1"/><stop offset="1" stop-color="#e9f6fb"/></linearGradient></defs>
        <g stroke="#e3e7eb" stroke-width="1"><line x1="32" y1="100" x2="32" y2="248"/><line x1="85" y1="100" x2="85" y2="248"/><line x1="138" y1="100" x2="138" y2="248"/><line x1="193" y1="100" x2="193" y2="248"/><line x1="241" y1="100" x2="241" y2="248"/><line x1="288" y1="100" x2="288" y2="248"/></g>
        <circle cx="240" cy="87" r="1.5" fill="var(--blue)"/>
        <path d="M0 126 C10 118,20 118,30 128 S50 122,60 130 S80 126,90 130 S110 146,120 150 S150 136,170 128 S190 120,200 130 S220 138,230 132 S250 140,265 158 S285 118,295 122 S320 140,329 150 L329 248 L0 248Z" fill="url(#sugarFill)"/>
        <path d="M0 126 C10 118,20 118,30 128 S50 122,60 130 S80 126,90 130 S110 146,120 150 S150 136,170 128 S190 120,200 130 S220 138,230 132 S250 140,265 158 S285 118,295 122 S320 140,329 150" fill="none" stroke="#2aa0d8" stroke-width="1.5"/>
      </svg>
      <div class="tip" style="left:182px;top:99px;padding:2px 10px"><span style="color:var(--blue);font-weight:600">10:</span> Low sugar in fri</div>
    </div>

    <div class="card" style="top:387px;height:248px">
      <div class="card-title">Daily Walk/Exercise</div>
      <div class="axis" style="left:8px;top:65px">50</div>
      <div class="axis" style="left:8px;top:143px">30</div>
      <div class="axis" style="left:8px;top:220px">10</div>
      <svg class="abs" style="left:0;top:0" width="329" height="248" viewBox="0 0 329 248">
        <g stroke="#eceff2"><line x1="39" y1="71" x2="312" y2="71"/><line x1="39" y1="149" x2="312" y2="149"/><line x1="39" y1="227" x2="312" y2="227"/></g>
        <rect x="61" y="149" width="17" height="78" rx="2" fill="var(--bar-idle)"/>
        <rect x="107" y="88" width="17" height="139" rx="2" fill="var(--bar-idle)"/>
        <rect x="154" y="139" width="17" height="88" rx="2" fill="var(--bar-idle)"/>
        <rect x="200" y="120" width="17" height="107" rx="2" fill="var(--blue)"/>
        <rect x="246" y="103" width="17" height="124" rx="2" fill="var(--bar-idle)"/>
        <rect x="292" y="172" width="17" height="55" rx="2" fill="var(--bar-idle)"/>
      </svg>
      <div class="tip" style="left:141px;top:58px;width:131px;height:43px;padding:5px 9px">
        <div style="font-size:11px;font-weight:600;color:#333">2000 Steps</div>
        <div style="margin-top:5px;color:#777">Monday, April 22nd</div>
      </div>
    </div>

    <div class="stat" style="left:24px">
      <div class="stat-head"><span class="stat-badge" style="background:var(--blue)"><svg width="14" height="14" viewBox="0 0 24 24" fill="none" stroke="#fff" stroke-width="2"><path d="M12 3c4 5 6 8 6 11a6 6 0 0 1-12 0c0-3 2-6 6-11z"/></svg></span><span class="stat-value">121</span><span class="stat-unit"><span style="font-size:15px">/56</span> bpm</span></div>
      <div class="stat-note">Sugar Bite Sent Weekly</div>
    </div>
    <div class="stat" style="left:196px">
      <div class="stat-head"><span class="stat-badge" style="background:var(--teal)"><svg width="14" height="14" viewBox="0 0 24 24" fill="none" stroke="#fff" stroke-width="2"><path d="M12 20s-8-5-8-11a4 4 0 0 1 8-1 4 4 0 0 1 8 1c0 6-8 11-8 11z"/></svg></span><span class="stat-value">110</span><span class="stat-unit" style="font-size:15px">Bpm</span></div>
      <div class="stat-note" style="font-size:12px;top:45px">Weekly Avg.</div>
    </div>

    <nav class="tabbar" style="top:776px">
      <div class="tab tab--current" style="left:17px;top:17px"><svg width="18" height="18" viewBox="0 0 24 24" fill="#333"><path d="M12 3l9 7v11H3V10z"/><circle cx="12" cy="14" r="2" fill="#fff"/></svg>Home</div>
      <div class="tab tab--active" style="left:81px;top:17px"><svg width="18" height="18" viewBox="0 0 24 24" fill="none" stroke="var(--amber)" stroke-width="1.6"><path d="M3 3v18h18"/><path d="M6 16l4-5 4 3 6-7"/></svg>Monitors</div>
      <div class="tab" style="left:224px;top:17px"><svg width="18" height="18" viewBox="0 0 24 24" fill="none" stroke="#333" stroke-width="1.6"><rect x="4" y="3" width="16" height="18" rx="3"/><path d="M9 3v18M15 9l-2 3 2 3"/></svg>Goal</div>
      <div class="tab" style="left:288px;top:17px"><svg width="18" height="18" viewBox="0 0 24 24" fill="none" stroke="#333" stroke-width="1.6"><circle cx="12" cy="8" r="4"/><path d="M4 21a8 8 0 0 1 16 0"/></svg>Profile</div>
      <div class="home-indicator" style="left:124px;top:69px"></div>
    </nav>
    <div class="fab" style="left:166px;top:755px"><svg width="20" height="20" viewBox="0 0 20 20" stroke="#fff" stroke-width="2"><path d="M10 2v16M2 10h16"/></svg></div>
  </section>

  <!-- Rehab Plan -->
  <section class="screen screen--plan">
    <span class="status-time">9:41</span>
    <svg class="status-icons" width="66" height="12" viewBox="0 0 66 12" fill="#111"><rect x="0" y="8" width="3" height="4" rx="1"/><rect x="5" y="6" width="3" height="6" rx="1"/><rect x="10" y="3" width="3" height="9" rx="1"/><rect x="15" y="0" width="3" height="12" rx="1"/><path d="M30 11l-2-2a3 3 0 0 1 4 0z M25 6a7.5 7.5 0 0 1 10 0l-1.5 1.5a5.5 5.5 0 0 0-7 0z M22 3a12 12 0 0 1 16 0l-1.5 1.5a10 10 0 0 0-13 0z"/><rect x="44" y="1" width="20" height="10" rx="3" fill="none" stroke="#111"/><rect x="46" y="3" width="16" height="6" rx="1.5"/></svg>
    <svg class="nav-back" width="12" height="18" viewBox="0 0 12 18" fill="none" stroke="#333" stroke-width="1.6"><path d="M9 2L3 9l6 7"/></svg>
    <div class="nav-title">Rehab Plan</div>
    <div class="portrait" role="img" aria-label="Portrait photo of the care advisor"></div>
    <div class="plan-title">Rehab Plan</div>
    <div class="plan-sub">See your plan to achieve no medicine diabetes control</div>
    <div class="steps-title">Create your plan in just a few steps</div>
    <div class="step" style="top:414px"><svg width="20" height="20" viewBox="0 0 24 24" fill="var(--blue)"><rect x="3" y="5" width="18" height="16" rx="2"/><rect x="6" y="2" width="2" height="5" rx="1"/><rect x="16" y="2" width="2" height="5" rx="1"/><g fill="#fff"><rect x="6" y="11" width="3" height="2"/><rect x="10.5" y="11" width="3" height="2"/><rect x="15" y="11" width="3" height="2"/><rect x="6" y="15" width="3" height="2"/><rect x="10.5" y="15" width="3" height="2"/></g></svg>Choose desired date</div>
    <div class="step" style="top:483px"><svg width="20" height="20" viewBox="0 0 24 24" fill="var(--blue)"><rect x="4" y="4" width="13" height="17" rx="2"/><rect x="7" y="2" width="7" height="4" rx="1"/><g fill="#fff"><rect x="7" y="10" width="7" height="1.6"/><rect x="7" y="14" width="5" height="1.6"/></g><circle cx="18" cy="17" r="4"/></svg>Follow suggested diet</div>
    <div class="step" style="top:552px"><svg width="20" height="20" viewBox="0 0 24 24" fill="var(--blue)"><rect x="3" y="2" width="13" height="18" rx="2"/><circle cx="13" cy="13" r="5" fill="#fff" stroke="var(--blue)" stroke-width="2"/><path d="M16.5 16.5L21 21" stroke="var(--blue)" stroke-width="2.4"/></svg><span>Enter your readings <small>(Sugar, Frequency, Diet)</small></span></div>

    <nav class="tabbar" style="top:731px">
      <div class="tab tab--current" style="left:17px;top:17px"><svg width="18" height="18" viewBox="0 0 24 24" fill="#333"><path d="M12 3l9 7v11H3V10z"/><circle cx="12" cy="14" r="2" fill="#fff"/></svg>Home</div>
      <div class="tab tab--active" style="left:81px;top:17px"><svg width="18" height="18" viewBox="0 0 24 24" fill="none" stroke="var(--amber)" stroke-width="1.6"><path d="M3 3v18h18"/><path d="M6 16l4-5 4 3 6-7"/></svg>Monitors</div>
      <div class="tab" style="left:224px;top:17px"><svg width="18" height="18" viewBox="0 0 24 24" fill="none" stroke="#333" stroke-width="1.6"><rect x="4" y="3" width="16" height="18" rx="3"/><path d="M9 3v18M15 9l-2 3 2 3"/></svg>Goal</div>
      <div class="tab" style="left:288px;top:17px"><svg width="18" height="18" viewBox="0 0 24 24" fill="none" stroke="#333" stroke-width="1.6"><circle cx="12" cy="8" r="4"/><path d="M4 21a8 8 0 0 1 16 0"/></svg>Profile</div>
      <div class="home-indicator" style="left:124px;top:69px"></div>
    </nav>
    <div class="fab" style="left:166px;top:710px"><svg width="20" height="20" viewBox="0 0 20 20" stroke="#fff" stroke-width="2"><path d="M10 2v16M2 10h16"/></svg></div>
  </section>

</div>
</body>
</html>
```